Whitcombe Business Card Design

The name of the business is Dario Whitcombe, CPA LLC
The service that we offer is Accounting, Tax & Consulting Services. I need it to have the following items:
Dario Whitcombe, Principal
Phone Number
Email Address
Physical Address

I have attached the company logo, one in black and one in white. Please provide a design in black background and the other in white background. Please include "Accounting, Tax & Consulting Services". I want the business card to be clean and very professional.

```html
<!DOCTYPE html>
<html lang="en">
<head>
<meta charset="utf-8">
<title>Dario Whitcombe, CPA LLC – Business Card</title>
<link rel="stylesheet" href="https://fonts.googleapis.com/css2?family=Mulish:wght@400;500;600&display=swap">
<style>
  :root {
    --backdrop: #202124;
    --card: #e9eaeb;
    --brand-red: #9b1c1f;
    --ink: #48494c;
    --ink-soft: #6d6e71;
    --white: #ffffff;
  }
  * { box-sizing: border-box; margin: 0; padding: 0; }
  html, body {
    width: 1200px; height: 1200px; overflow: hidden;
    background: var(--backdrop);
    font-family: "Mulish", sans-serif;
  }
  .canvas { position: relative; width: 1200px; height: 1200px; }
  .card {
    position: absolute; left: 252px; width: 744px; height: 428px;
    background: var(--card); overflow: hidden;
  }
  .card--front { top: 172px; }
  .card--back { top: 647px; }
  .card__shape { position: absolute; inset: 0; }

  .person { position: absolute; left: 109px; top: 40px; }
  .person__name {
    font-size: 23px; font-weight: 500; letter-spacing: 0.5px;
    color: var(--ink); text-transform: uppercase;
  }
  .person__name .first { color: var(--brand-red); }
  .person__role { font-size: 15px; color: var(--ink); margin-top: 6px; }

  .address {
    position: absolute; left: 139px; top: 258px;
    font-size: 16px; line-height: 25px; color: var(--brand-red);
  }
  .contacts { position: absolute; left: 0; top: 320px; list-style: none; }
  .contacts li {
    display: flex; align-items: center; height: 25px;
    font-size: 16px; color: var(--ink);
  }
  .contacts svg { width: 13px; height: 13px; margin-left: 103px; margin-right: 23px; }

  .company {
    position: absolute; display: flex; align-items: center; gap: 10px;
    color: var(--ink); font-weight: 600; white-space: nowrap;
  }
  .company__square { background: var(--brand-red); flex: none; }
  .company--front { right: 22px; bottom: 40px; font-size: 15px; }
  .company--front .company__square { width: 14px; height: 14px; }
  .company--back { left: 50%; top: 180px; transform: translateX(-50%); font-size: 30px; gap: 16px; }
  .company--back .company__square { width: 30px; height: 30px; }

  .services {
    position: absolute; left: 116px; width: 493px; top: 346px;
    text-align: center; font-size: 23px; color: var(--white);
  }
</style>
</head>
<body>
<main class="canvas">

  <section class="card card--front" aria-label="Business card front">
    <svg class="card__shape" viewBox="0 0 744 428" aria-hidden="true">
      <path fill="var(--brand-red)" d="M0 0 H75 V102 Q75 124 97 126 H109 Q129 128 129 150 V428 H0 Z"/>
    </svg>

    <div class="person">
      <h1 class="person__name"><span class="first">Dario</span> Whitcombe</h1>
      <p class="person__role">Principal</p>
    </div>

    <address class="address">
      Po box 5830 Larkfield<br>
      brookvale, ab t5k-3r8
    </address>

    <ul class="contacts">
      <li>
        <svg viewBox="0 0 24 24" aria-hidden="true"><path fill="var(--white)" d="M6.6 10.8a15.1 15.1 0 0 0 6.6 6.6l2.2-2.2a1 1 0 0 1 1-.25 11.4 11.4 0 0 0 3.6.57 1 1 0 0 1 1 1V20a1 1 0 0 1-1 1A17 17 0 0 1 3 4a1 1 0 0 1 1-1h3.5a1 1 0 0 1 1 1c0 1.25.2 2.45.57 3.57a1 1 0 0 1-.25 1z"/></svg>
        780 (0) 555 204 318
      </li>
      <li>
        <svg viewBox="0 0 24 24" aria-hidden="true"><rect x="2" y="5" width="20" height="14" fill="var(--white)"/><path d="M2 5 L12 13 L22 5" fill="none" stroke="var(--brand-red)" stroke-width="2"/></svg>
        hello(@)whitcombecpa.com
      </li>
      <li>
        <svg viewBox="0 0 24 24" aria-hidden="true"><circle cx="12" cy="12" r="10" fill="var(--white)"/><path d="M2 12 H22 M12 2 C7 7 7 17 12 22 M12 2 C17 7 17 17 12 22" fill="none" stroke="var(--brand-red)" stroke-width="1.6"/></svg>
        www.whitcombecpa.com
      </li>
    </ul>

    <div class="company company--front">
      <span class="company__square" aria-hidden="true"></span>
      Dario Whitcombe, CPA LLC
    </div>
  </section>

  <section class="card card--back" aria-label="Business card back">
    <svg class="card__shape" viewBox="0 0 744 428" aria-hidden="true">
      <path fill="var(--brand-red)" d="M0 390 H100 Q116 390 116 374 V358 Q116 342 132 342 H593 Q609 342 609 358 V374 Q609 390 625 390 H744 V428 H0 Z"/>
    </svg>

    <div class="company company--back">
      <span class="company__square" aria-hidden="true"></span>
      Dario Whitcombe, CPA LLC
    </div>

    <p class="services">Accounting, Tax &amp; Consulting Services</p>
  </section>

</main>
</body>
</html>
```